PHD-project

i need the figures to be in the same stile. info is inside the file. There are 5 figures that need redesign. this is for PhD.

Target Market(s)

it will be used in my phd

Colors

```html
<!DOCTYPE html>
<html lang="en">
<head>
<meta charset="utf-8">
<title>Reflection – Elements and Modes</title>
<link rel="stylesheet" href="https://fonts.googleapis.com/css2?family=Roboto:wght@300;700&display=swap">
<style>
  :root {
    --ring-red: #ED1C24;
    --core-blue: #4AB0E5;
    --mode-light: #AADFF4;
    --mode-deep: #8DB6DC;
    --ink: #000000;
    --text-grey: #231F20;
    --paper: #FFFFFF;
  }
  html, body {
    margin: 0;
    padding: 0;
    overflow: hidden;
    background: var(--paper);
  }
  .canvas {
    width: 1200px;
    height: 1200px;
    display: block;
  }
  .element-label,
  .mode-label {
    font-family: "Roboto", Arial, sans-serif;
    font-weight: 700;
    font-size: 30px;
    fill: var(--ink);
  }
  .mode-label { text-anchor: middle; }
  .definition {
    font-family: "Roboto", Arial, sans-serif;
    font-weight: 300;
    font-size: 25px;
    fill: var(--text-grey);
  }
  .outer-ring { fill: none; stroke: var(--ring-red); stroke-width: 52; }
  .core-circle { fill: var(--core-blue); opacity: 0.93; }
  .bullet { fill: var(--ink); }
</style>
</head>
<body>
<svg class="canvas" viewBox="0 0 1500 1500" xmlns="http://www.w3.org/2000/svg">
  <defs>
    <linearGradient id="modeFill" x1="0" y1="0" x2="1" y2="0">
      <stop offset="0" stop-color="var(--mode-light)" style="stop-color:#AADFF4"/>
      <stop offset="1" stop-color="var(--mode-deep)" style="stop-color:#8DB6DC"/>
    </linearGradient>
  </defs>

  <circle class="outer-ring" cx="549" cy="670" r="376"/>

  <g class="modes">
    <circle class="mode-circle" cx="889" cy="522" r="174" fill="url(#modeFill)"/>
    <circle class="mode-circle" cx="902" cy="907" r="174" fill="url(#modeFill)"/>
  </g>

  <circle class="core-circle" cx="549" cy="670" r="322"/>

  <g class="elements">
    <circle class="bullet" cx="347" cy="557" r="13"/>
    <text class="element-label" x="379" y="568">Reflection involves</text>
    <text class="element-label" x="379" y="607">three elements</text>

    <circle class="bullet" cx="347" cy="675" r="13"/>
    <text class="element-label" x="379" y="686">Returing to experience</text>

    <circle class="bullet" cx="347" cy="753" r="13"/>
    <text class="element-label" x="379" y="764">Attending to feeling</text>

    <circle class="bullet" cx="347" cy="832" r="13"/>
    <text class="element-label" x="379" y="843">Evaluating experience</text>
  </g>

  <text class="mode-label" x="935" y="505">Reflecting</text>
  <text class="mode-label" x="939" y="545">on action</text>

  <text class="mode-label" x="921" y="898">Reflecting</text>
  <text class="mode-label" x="925" y="937">in action</text>

  <g class="definition">
    <text x="1063" y="666">Reflection is an active process</text>
    <text x="1063" y="698">of witnessing one’s can</text>
    <text x="1063" y="730">experience in order to examine</text>
    <text x="1063" y="762">it more closely, give meaning to</text>
    <text x="1063" y="793">it, and learn from it.</text>
  </g>
</svg>
</body>
</html>
```